Investment company needing business card

We are wanting a business card which looks sharp and easy on the eye. We are thinking of having a business card with the logo embossed on it, to really make it stand out. We will only have a small amount of information of the business card, person's name, position, email address and phone number

Contact Information for Business Card

Danielle Frost
Executive Assistant
+64 21 473 5162
danielf@harwickpartners.co.nz

Requirements
Must have
• Embossed logo
Should not have
• Not to be busy

```html
<!DOCTYPE html>
<html lang="en">
<head>
<meta charset="utf-8">
<title>Harwick Partners – Business Card</title>
<link rel="stylesheet" href="https://fonts.googleapis.com/css2?family=Roboto:wght@400;500;700&display=swap">
<style>
  :root {
    --backdrop: #3b3b3b;
    --card: #ececec;
    --brand-green: #22b66d;
    --brand-grey: #636363;
    --text-grey: #555555;
  }
  * { margin: 0; padding: 0; box-sizing: border-box; }
  html, body {
    width: 1200px;
    height: 799px;
    overflow: hidden;
    background: var(--backdrop);
    font-family: "Roboto", Arial, sans-serif;
  }
  .stage {
    width: 1200px;
    height: 799px;
    display: flex;
    align-items: center;
    justify-content: center;
  }
  .business-card {
    position: relative;
    width: 420px;
    height: 700px;
    background: var(--card);
    box-shadow: 0 10px 30px rgba(0,0,0,0.35);
    overflow: hidden;
  }
  .brand {
    position: absolute;
    top: 62px;
    left: 0;
    right: 0;
    display: flex;
    align-items: center;
    justify-content: center;
    gap: 12px;
  }
  .brand-square {
    width: 34px;
    height: 34px;
    background: var(--brand-green);
  }
  .brand-name {
    font-size: 26px;
    font-weight: 700;
    letter-spacing: 1px;
    color: var(--brand-green);
    text-transform: uppercase;
  }
  .contact-block {
    position: absolute;
    top: 150px;
    left: 0;
    right: 0;
    text-align: center;
  }
  .person-name {
    font-size: 30px;
    font-weight: 700;
    color: var(--brand-green);
    text-transform: uppercase;
    letter-spacing: 0.5px;
  }
  .person-role {
    margin-top: 4px;
    font-size: 17px;
    font-weight: 400;
    color: var(--text-grey);
    text-transform: uppercase;
    letter-spacing: 0.5px;
  }
  .divider {
    width: 34px;
    height: 2px;
    background: var(--text-grey);
    margin: 20px auto 22px;
  }
  .contact-line {
    font-size: 16px;
    line-height: 1.45;
    color: var(--text-grey);
  }
  .emboss-mark {
    position: absolute;
    left: 80px;
    bottom: 60px;
    width: 260px;
    height: 260px;
    background: var(--brand-grey);
  }
</style>
</head>
<body>
  <main class="stage">
    <article class="business-card">
      <header class="brand">
        <span class="brand-square" aria-hidden="true"></span>
        <span class="brand-name">Harwick Partners</span>
      </header>
      <section class="contact-block">
        <h1 class="person-name">Danielle Frost</h1>
        <p class="person-role">Executive Assistant</p>
        <div class="divider" aria-hidden="true"></div>
        <p class="contact-line">+64 21 473 5162</p>
        <p class="contact-line">danielf@harwickpartners.co.nz</p>
        <p class="contact-line">www.harwickpartners.co.nz</p>
      </section>
      <div class="emboss-mark" aria-hidden="true"></div>
    </article>
  </main>
</body>
</html>
```